Company Website Re-design for Software development consultancy

We would like our company website to be redesigned using our existing marketing collateral and website content as a guide

current site : www.brightkestrel.com.au

For the different pages types and content please base on the following site : https://www.quorvalabs.net/

We want a coded site - but will replace the content ourselves within the sections you provide to customise to our needs.

Target Market(s)

Medium to Large corporates needing software design and development services

Industry/Entity Type

Information Technology

Coding

Coded - Design and coding required

Number of Pages Required

5+ page

Font styles to use
Sans Serif

Colors
ec1f27
ffffff
000000

Requirements
Must have
• Align to colour scheme of existing collateral
• Include pages for the key areas of our busines - see : https://www.quorvalabs.net/
Nice to have
• image rotators - make the site interesting to the business visitor

```html
<!DOCTYPE html>
<html lang="en">
<head>
<meta charset="utf-8">
<title>Bright Kestrel – Blogs &amp; Articles</title>
<link rel="stylesheet" href="https://fonts.googleapis.com/css2?family=Poppins:wght@500;600&family=Mulish:wght@400;500;600&family=Open+Sans:wght@400;600&family=Roboto:wght@400;500&display=swap">
<style>
  :root {
    --brand-red: #ec1f27;
    --white: #ffffff;
    --black: #000000;
    --ink: #1a1a1a;
    --muted: #6b6b6b;
    --date-grey: #8a8a8a;
    --card-border: #e2e2e2;
    --footer-bg: #ececec;
    --footer-ink: #444444;
    --icon-grey: #555555;
  }
  * { box-sizing: border-box; margin: 0; padding: 0; }
  html, body { width: 738px; height: 1200px; overflow: hidden; background: var(--white); }
  body { position: relative; font-family: "Open Sans", Arial, sans-serif; color: var(--ink); }

  /* Hero */
  .hero {
    position: absolute; left: 0; top: 0; width: 738px; height: 270px;
    background:
      linear-gradient(rgba(20,20,22,.55), rgba(20,20,22,.62)),
      radial-gradient(ellipse at 55% 45%, #5a5f66 0%, #34373c 45%, #1d1f22 100%);
  }
  .brand {
    position: absolute; left: 112px; top: 18px;
    font-family: "Poppins", Arial, sans-serif; font-weight: 600; font-size: 19px; line-height: 26px;
    letter-spacing: .4px; color: var(--white); text-transform: uppercase; white-space: nowrap;
  }
  .main-nav a {
    position: absolute; top: 24px;
    font-family: "Roboto", Arial, sans-serif; font-size: 10.4px; font-weight: 400; line-height: 14px;
    color: var(--white); text-decoration: none; letter-spacing: .1px; white-space: nowrap;
  }
  .nav-about { left: 296px; }
  .nav-products { left: 362px; }
  .nav-blog { left: 499px; }
  .nav-contact { left: 587px; }
  .hero-title {
    position: absolute; left: 0; top: 146px; width: 730px; text-align: center;
    font-family: "Poppins", Arial, sans-serif; font-weight: 600; font-size: 31px;
    color: var(--white); letter-spacing: .3px;
  }

  /* Blog listing */
  .section-title {
    position: absolute; left: 114px; top: 302px;
    font-family: "Poppins", Arial, sans-serif; font-weight: 600; font-size: 18.5px; color: var(--black);
  }
  .blog-grid {
    position: absolute; left: 113px; top: 342px;
    display: grid; grid-template-columns: 251px 251px; column-gap: 10px; row-gap: 17px;
  }
  .blog-card {
    width: 251px; height: 245px; border: 1px solid var(--card-border);
    box-shadow: 0 1px 3px rgba(0,0,0,.08); background: var(--white);
  }
  .card-media { display: block; width: 100%; height: 123px; }
  .media-team { background: linear-gradient(135deg, #4a4c52, #8d8b88 55%, #2f3136); }
  .media-code { background: linear-gradient(120deg, #0c1f3d, #12406e 45%, #1f8fb8 100%); }
  .media-meeting { background: linear-gradient(135deg, #d9d7d2, #a49a8e 50%, #e8e6e2); }
  .media-laptop { background: linear-gradient(135deg, #c9c5bf, #e9e6e1 50%, #b7a99a); }
  .media-workshop { background: linear-gradient(135deg, #1f242b, #6c7076 55%, #2a2d33); }
  .media-tablet { background: linear-gradient(135deg, #e5e4e2, #9aa7b8 50%, #d8cbbb); }
  .card-body { padding: 10px 18px 0 19px; }
  .card-date { font-family: "Mulish", Arial, sans-serif; font-size: 7.6px; color: var(--date-grey); text-transform: uppercase; letter-spacing: .2px; }
  .blog-card.is-featured .card-date { color: var(--ink); font-weight: 500; }
  .card-title {
    margin-top: 7px; font-family: "Mulish", Arial, sans-serif; font-weight: 500;
    font-size: 11.6px; color: var(--brand-red);
  }
  .card-excerpt { margin-top: 6px; font-size: 6.9px; line-height: 12px; color: var(--muted); }
  .read-more {
    display: inline-block; margin-top: 6px; padding-bottom: 5px;
    font-family: "Mulish", Arial, sans-serif; font-size: 7.2px; font-weight: 600;
    color: var(--ink); text-decoration: none; text-transform: uppercase;
  }
  .blog-card.is-featured .read-more {
    background: linear-gradient(var(--brand-red), var(--brand-red)) left bottom / 26px 1.5px no-repeat;
  }
  .blog-card.is-featured.is-dark-rule .read-more {
    background: linear-gradient(var(--ink), var(--ink)) left bottom / 26px 1.5px no-repeat;
  }

  /* Footer */
  .site-footer {
    position: absolute; left: 0; top: 1154px; width: 738px; height: 46px; background: var(--footer-bg);
  }
  .footer-legal { position: absolute; left: 231px; top: 14px; font-size: 9.6px; color: var(--footer-ink); white-space: nowrap; }
  .footer-legal span + span { margin-left: 5px; }
  .social-links { position: absolute; left: 524px; top: 17px; display: flex; gap: 17px; }
  .social-links span { width: 12px; height: 12px; border-radius: 50%; background: var(--icon-grey); display: block; }
</style>
</head>
<body>
  <header class="hero" role="img" aria-label="Photo of a laptop showing a blog page on a wooden desk">
    <div class="brand">Bright Kestrel</div>
    <nav class="main-nav">
      <a class="nav-about" href="#">ABOUT US</a>
      <a class="nav-products" href="#">PRODUCTS AND SERVICES</a>
      <a class="nav-blog" href="#">BLOG ARTICLE</a>
      <a class="nav-contact" href="#">CONTACT</a>
    </nav>
    <h1 class="hero-title">BLOGS &amp; ARTICLES</h1>
  </header>

  <h2 class="section-title">LATEST BLOGS</h2>

  <main class="blog-grid">
    <article class="blog-card">
      <div class="card-media media-team" role="img" aria-label="Photo of developers gathered around a computer screen"></div>
      <div class="card-body">
        <p class="card-date">March 20, 2018</p>
        <h3 class="card-title">Class aptent taciti sociosqu ad litora</h3>
        <p class="card-excerpt">Praesent elementum elit at tellus nec ultricies sit amet porttitor mattis enim In massa libero interdum nec interdum vel blandit sed nulla In ullamcorper est eget tempor cursus</p>
        <a class="read-more" href="#">Read more</a>
      </div>
    </article>
    <article class="blog-card is-featured">
      <div class="card-media media-code" role="img" aria-label="Photo of source code on a blue screen"></div>
      <div class="card-body">
        <p class="card-date">March 20, 2018</p>
        <h3 class="card-title">Arquent per conubia nostra</h3>
        <p class="card-excerpt">Praesent elementum elit at tellus nec ultricies sit amet porttitor mattis enim In massa libero interdum nec interdum vel blandit sed nulla In ullamcorper est eget tempor cursus</p>
        <a class="read-more" href="#">Read more</a>
      </div>
    </article>
    <article class="blog-card">
      <div class="card-media media-meeting" role="img" aria-label="Photo of a team meeting around an office table"></div>
      <div class="card-body">
        <p class="card-date">March 20, 2018</p>
        <h3 class="card-title">Class aptent taciti sociosqu ad litora</h3>
        <p class="card-excerpt">Praesent elementum elit at tellus nec ultricies sit amet porttitor mattis enim In massa libero interdum nec interdum vel blandit sed nulla In ullamcorper est eget tempor cursus</p>
        <a class="read-more" href="#">Read more</a>
      </div>
    </article>
    <article class="blog-card is-featured">
      <div class="card-media media-laptop" role="img" aria-label="Photo of colleagues reviewing work at a laptop"></div>
      <div class="card-body">
        <p class="card-date">March 20, 2018</p>
        <h3 class="card-title">Arquent per conubia nostra</h3>
        <p class="card-excerpt">Praesent elementum elit at tellus nec ultricies sit amet porttitor mattis enim In massa libero interdum nec interdum vel blandit sed nulla In ullamcorper est eget tempor cursus</p>
        <a class="read-more" href="#">Read more</a>
      </div>
    </article>
    <article class="blog-card">
      <div class="card-media media-workshop" role="img" aria-label="Photo of a group working together over laptops"></div>
      <div class="card-body">
        <p class="card-date">March 20, 2018</p>
        <h3 class="card-title">Class aptent taciti sociosqu ad litora</h3>
        <p class="card-excerpt">Praesent elementum elit at tellus nec ultricies sit amet porttitor mattis enim In massa libero interdum nec interdum vel blandit sed nulla In ullamcorper est eget tempor cursus</p>
        <a class="read-more" href="#">Read more</a>
      </div>
    </article>
    <article class="blog-card is-featured is-dark-rule">
      <div class="card-media media-tablet" role="img" aria-label="Photo of three colleagues looking at a tablet"></div>
      <div class="card-body">
        <p class="card-date">March 20, 2018</p>
        <h3 class="card-title">Arquent per conubia nostra</h3>
        <p class="card-excerpt">Praesent elementum elit at tellus nec ultricies sit amet porttitor mattis enim In massa libero interdum nec interdum vel blandit sed nulla In ullamcorper est eget tempor cursus</p>
        <a class="read-more" href="#">Read more</a>
      </div>
    </article>
  </main>

  <footer class="site-footer">
    <p class="footer-legal"><span>© 2018 Company Name</span><span>All right reserved</span><span>Term of Use</span></p>
    <div class="social-links" aria-label="Social links">
      <span></span><span></span><span></span><span></span>
    </div>
  </footer>
</body>
</html>
```